Larkfield Heating Services, needs a business card Design

We need a business card design for a company in the United Kingdom, we work mainly in London in Domestic Plumbing & Heating and would like to branch out (more) in to the Commercial aspect of the business.
We need the card to promote care, trust, professionalism, because we do, if possible, we will always better or match prices with an over all better experience for clients.

Info to add on card...

My name... Dorian Welk
Cell... 07491365817
Email... dorianwelk00@Postrun.com
Business/Post code... NW18 4TB

Thanks

Dorian

Hi there updated my design project! If you could please look through again and add as much as possable (as you will see) I'd be very grateful! Although I do enjoy seeing all your fantastic designs, I don't want to spend the remaining 14 days being hard to please. PS.. I'm from NZ but living in UK, if you find patriotic (NZ) that is do add in. Not of huge importance but It dose get peoples attention! Thanks a lot, Dorian

I work in Chelsea and most of my days so think Chelsea.

Thanks.

Business

Serif
Sans Serif

• Just want text to be as easy to read as possible!

Would like to see some or all pictures I have on the card if at all possible.
They are well known logos in my industry.
And my team and I are all fully qualified in these different schemes.

Also a break down of services I provide!

- Central Heating Engineering.
- Bathroom and Kitchen Fitting.
- Plumbing.
- Electrical.
- Tiling.
- All Your Carpentry and Building Needs.

Thanks.

• Only restriction no pink otherwise go for it!

Thanks.

```html
<!DOCTYPE html>
<html lang="en">
<head>
<meta charset="utf-8">
<title>Larkfield Heating Services – Business Card</title>
<link rel="stylesheet" href="https://fonts.googleapis.com/css2?family=Exo+2:wght@400;500;600&display=swap">
<style>
  :root {
    --backdrop: #6e6e6e;
    --card-white: #f4f5f6;
    --blue: #1a7fc8;
    --blue-deep: #1467ad;
    --blue-light: #2a9ad8;
    --green: #5cbf3a;
    --text-blue: #1a6fc0;
    --ink-white: #ffffff;
  }
  * { box-sizing: border-box; margin: 0; padding: 0; }
  html, body {
    width: 1200px; height: 750px; overflow: hidden;
    background: var(--backdrop);
  }
  .sheet {
    width: 1200px; height: 750px;
    display: flex; align-items: center; justify-content: center; gap: 40px;
  }
  .card {
    position: relative; width: 560px; height: 320px;
    background: var(--card-white); overflow: hidden;
    box-shadow: 0 8px 24px rgba(0,0,0,.35);
  }
  .card-shapes { position: absolute; inset: 0; width: 100%; height: 100%; }
  .brand {
    position: absolute; display: flex; align-items: center; gap: 12px;
  }
  .brand-dot {
    width: 40px; height: 40px; border-radius: 50%;
    background: var(--blue); flex: none;
  }
  .brand-name {
    font-family: "Exo 2", sans-serif; font-weight: 500;
    color: var(--text-blue); font-size: 20px; line-height: 1.2;
    white-space: nowrap;
  }
  .front .brand { left: 62px; top: 92px; }
  .website {
    position: absolute; right: 18px; top: 157px;
    font-family: "Exo 2", sans-serif; font-size: 13px; letter-spacing: 1.5px;
    color: var(--ink-white);
  }
  .back .brand { right: 26px; top: 86px; }
  .back .brand-name { font-size: 17px; }
  .person {
    position: absolute; left: 30px; top: 64px; color: var(--ink-white);
    font-family: "Exo 2", sans-serif;
  }
  .person-name { font-size: 21px; font-weight: 500; letter-spacing: 1.5px; text-transform: uppercase; }
  .person-role { font-size: 14px; margin-top: 2px; padding-left: 14px; }
  .contacts {
    position: absolute; left: 28px; bottom: 20px; list-style: none;
    font-family: "Exo 2", sans-serif; font-size: 11.5px; color: var(--ink-white);
  }
  .contacts li { display: flex; align-items: center; gap: 8px; height: 19px; }
  .contacts svg { width: 13px; height: 13px; flex: none; }
</style>
</head>
<body>
<main class="sheet">

  <section class="card front" aria-label="Card front">
    <svg class="card-shapes" viewBox="0 0 560 320" aria-hidden="true">
      <defs>
        <linearGradient id="bandGrad" x1="0" x2="1">
          <stop offset="0" stop-color="#1467ad"/>
          <stop offset=".55" stop-color="#2a9ad8"/>
          <stop offset="1" stop-color="#1467ad"/>
        </linearGradient>
        <radialGradient id="cornerGrad" cx=".7" cy=".3" r=".8">
          <stop offset="0" stop-color="#2a9ad8"/>
          <stop offset="1" stop-color="#1467ad"/>
        </radialGradient>
      </defs>
      <path d="M452 0 C410 50 425 128 505 150 L560 150 L560 0 Z" fill="var(--green)"/>
      <path d="M470 0 C432 45 445 122 520 147 L560 150 L560 0 Z" fill="url(#cornerGrad)"/>
      <rect x="300" y="148" width="260" height="32" fill="var(--blue-deep)"/>
      <rect x="0" y="180" width="560" height="4" fill="var(--green)"/>
      <rect x="0" y="184" width="560" height="52" fill="url(#bandGrad)"/>
    </svg>
    <div class="brand">
      <span class="brand-dot"></span>
      <p class="brand-name">Larkfield Heating Services</p>
    </div>
    <p class="website">www.larkfieldheat.co.uk</p>
  </section>

  <section class="card back" aria-label="Card back">
    <svg class="card-shapes" viewBox="0 0 560 320" aria-hidden="true">
      <defs>
        <radialGradient id="backGrad" cx=".35" cy=".45" r=".75">
          <stop offset="0" stop-color="#2a9ad8"/>
          <stop offset="1" stop-color="#1467ad"/>
        </radialGradient>
      </defs>
      <rect width="560" height="320" fill="url(#backGrad)"/>
      <path d="M232 0 C280 185 410 258 560 268 L560 0 Z" fill="var(--green)"/>
      <path d="M252 0 C300 170 420 236 560 246 L560 0 Z" fill="var(--card-white)"/>
    </svg>
    <div class="person">
      <p class="person-name">Dorian Welk</p>
      <p class="person-role">Managing Director</p>
    </div>
    <div class="brand">
      <span class="brand-dot"></span>
      <p class="brand-name">Larkfield Heating Services</p>
    </div>
    <ul class="contacts">
      <li><svg viewBox="0 0 16 16"><circle cx="8" cy="8" r="8" fill="#fff"/><path d="M5 4.5l1.6-.5 1 2-1 .8a5 5 0 0 0 2.6 2.6l.8-1 2 1-.5 1.6C8 11.5 4.5 8 5 4.5z" fill="#1467ad"/></svg>07491 365817</li>
      <li><svg viewBox="0 0 16 16"><circle cx="8" cy="8" r="8" fill="#fff"/><rect x="5.5" y="3.5" width="5" height="9" rx="1" fill="#1467ad"/></svg>07491 365817</li>
      <li><svg viewBox="0 0 16 16"><circle cx="8" cy="8" r="8" fill="#fff"/><rect x="4" y="5" width="8" height="6" fill="#1467ad"/><path d="M4 5l4 3.2L12 5" stroke="#fff" fill="none"/></svg>dorianwelk00@Postrun.com</li>
      <li><svg viewBox="0 0 16 16"><circle cx="8" cy="8" r="8" fill="#fff"/><circle cx="8" cy="8" r="4.2" fill="none" stroke="#1467ad"/><path d="M3.8 8h8.4M8 3.8c-2 2.6-2 5.8 0 8.4M8 3.8c2 2.6 2 5.8 0 8.4" stroke="#1467ad" fill="none" stroke-width=".8"/></svg>www.larkfieldheat.co.uk</li>
      <li><svg viewBox="0 0 16 16"><circle cx="8" cy="8" r="8" fill="#fff"/><path d="M8 12.5S5 9 5 6.8a3 3 0 0 1 6 0C11 9 8 12.5 8 12.5z" fill="#1467ad"/><circle cx="8" cy="6.8" r="1" fill="#fff"/></svg>14 Larch Row, London NW18 4TB</li>
    </ul>
  </section>

</main>
</body>
</html>
```